Creation of brand identity and website "Tandem K"

I am currently seeking an brand, identity and web design for a new project called Tandem K. This is a brand new concept from scratch and you have free-reign on the whole design process, taking into account my preference below.

Must include the name "Tandem K", or "Tandem K: Or the year I woke Up". Kudos is this forms part of the brands logo

Design that can be easily scaled to potentially include: a blog, timeline and vlogs.

Minimal but effective use of colour (however any colours and combinations permitted

Use of icons/graphics over text wherever possible

Minimal use of frames and borders

I appreciate this is a fairly wide scope so please contact me on marblefinch@postwillow.com with any questions or more information on what the project is.

Target Market(s)

Male and Female 20-40
Blog readers
Selfhelp

Industry/Entity Type

Seeking

Number of Pages Required

1 page

Font styles to use
Serif
Sans Serif

Requirements
Must have
• It is in effect a blog design, so about me section, recent blog / archived posts, reader comments / Q and A section.
• A coded design would be appreciated to make my life easier however I have left the design as uncoded as getting the right design matters more to me and I want to keep the project open to as many designers as possible
Nice to have
• See project description for other details and please ask if you need anything else :)
Should not have
• Mustn't be cluttered or feel fussy
• Promote icons over text
• Frames / multiple borders

```html
<!DOCTYPE html>
<html lang="en">
<head>
<meta charset="utf-8">
<title>Tandem K</title>
<link rel="stylesheet" href="https://fonts.googleapis.com/css2?family=Josefin+Sans:wght@600;700&family=Lato:wght@400;700&display=swap">
<style>
:root{
  --navy:#24395f;
  --orange:#f04924;
  --text:#5b6170;
  --rule:#d9d9d9;
  --light:#ebebeb;
  --white:#fff;
}
*{box-sizing:border-box;margin:0;padding:0}
html,body{width:687px;height:1200px;overflow:hidden;background:var(--white)}
body{position:relative;font-family:"Lato",sans-serif;color:var(--text)}
.abs{position:absolute}
.head-font{font-family:"Josefin Sans",sans-serif}
/* header */
.logo{left:68px;top:10px;font:700 21px "Josefin Sans",sans-serif;color:var(--navy);letter-spacing:.3px}
.search{display:flex;border:1px solid var(--navy);height:18px}
.search span{flex:1;font-size:10px;padding:2px 6px;color:#8a8f9a}
.search b{width:36px;background:var(--orange);display:flex;align-items:center;justify-content:center}
.top-search{left:426px;top:14px;width:192px}
.nav{left:0;top:46px;width:687px;height:28px;background:var(--navy)}
.nav ul{list-style:none;position:absolute;left:69px;top:0;display:flex;height:28px}
.nav li{font:700 9.5px "Josefin Sans",sans-serif;color:var(--white);padding:0 11px;line-height:29px;letter-spacing:.3px}
.nav li.active{background:var(--orange);padding:0 12px;width:74px}
.social{position:absolute;left:544px;top:7px;display:flex;gap:7px}
.social i{width:14px;height:14px;border-radius:50%;background:var(--orange);display:block}
/* posts */
.photo{display:block}
.meta{font-size:8.5px;color:var(--navy);display:flex;align-items:center;gap:3px;letter-spacing:.3px}
.meta strong{font-weight:700}
.title{font:700 15px "Josefin Sans",sans-serif;color:var(--navy);line-height:1.05}
.excerpt{font-size:9.5px;line-height:13px;letter-spacing:.2px}
.btn{border:1px solid var(--orange);color:var(--orange);font:700 8.5px "Lato",sans-serif;display:flex;align-items:center;justify-content:center;width:70px;height:21px;letter-spacing:.3px}
.rule{height:1px;background:var(--rule)}
.hero-caption{left:82px;top:145px;font:700 14px "Josefin Sans",sans-serif;color:var(--navy)}
.hero-caption em{font-style:normal;color:var(--orange)}
.arrows{left:384px;top:255px;display:flex;gap:10px}
.load{left:69px;top:940px;width:357px;height:25px;background:#d0d0d0;font-size:9px;color:#333;display:flex;align-items:center;justify-content:center;gap:6px}
/* sidebar */
.widget-head{width:155px;height:19px}
.widget-head span{position:absolute;left:7px;top:3px;font:700 11px "Josefin Sans",sans-serif;color:var(--white);letter-spacing:.3px}
.pop-title{font:700 8.5px "Josefin Sans",sans-serif;color:var(--navy);letter-spacing:.5px}
.pop-text{font-size:7.5px;line-height:9.5px;color:#333;margin-top:4px}
.avatar{width:53px;height:53px;border-radius:50%}
.tags{left:448px;top:681px;width:175px;display:flex;flex-wrap:wrap;gap:5px 4px}
.tags span{background:var(--navy);color:var(--white);font-size:7px;padding:4px 6px;line-height:8px}
.archive{left:448px;top:811px;list-style:none}
.archive li{display:flex;align-items:center;gap:8px;height:21.6px;font:700 10px "Josefin Sans",sans-serif;color:var(--navy);text-decoration:underline}
/* about */
.about{left:0;top:982px;width:687px;height:184px;background:var(--light)}
.about h2{left:249px;top:12px;font:700 20px "Josefin Sans",sans-serif;color:var(--navy)}
.about p{left:249px;top:45px;width:370px;font-size:9.4px;line-height:12.5px;letter-spacing:.3px}
.footer{left:0;top:1166px;width:687px;height:34px;background:var(--navy);color:var(--white);font:700 8.5px "Lato",sans-serif;text-align:center;line-height:34px;letter-spacing:.3px}
</style>
</head>
<body>
<svg width="0" height="0" style="position:absolute">
  <symbol id="clock" viewBox="0 0 10 10"><circle cx="5" cy="5" r="4" fill="none" stroke="#f04924" stroke-width="1"/><path d="M5 2.6V5h1.8" fill="none" stroke="#f04924" stroke-width="1"/></symbol>
  <symbol id="glass" viewBox="0 0 10 10"><circle cx="4.2" cy="4.2" r="3" fill="none" stroke="#fff" stroke-width="1.4"/><path d="M6.4 6.4 9 9" stroke="#fff" stroke-width="1.4"/></symbol>
  <symbol id="banner" viewBox="0 0 155 19"><polygon points="0,0 136,0 150,19 0,19" fill="#f04924"/><polyline points="120,0.6 142,0.6 154,18.4" fill="none" stroke="#24395f" stroke-width="1.2"/></symbol>
</svg>

<header>
  <div class="abs logo">Tandem K</div>
  <div class="abs search top-search"><span>Search</span><b><svg width="9" height="9"><use href="#glass"/></svg></b></div>
  <nav class="abs nav">
    <ul><li class="active">About Me</li><li>Recent Blog</li><li>Reader Comments</li><li>Contact Us</li></ul>
    <div class="social"><i></i><i></i><i></i><i></i></div>
  </nav>
</header>

<main>
  <div class="abs photo" style="left:69px;top:79px;width:357px;height:200px;background:linear-gradient(180deg,#a9c9e0 0%,#e3d6b6 45%,#4f7f8c 58%,#c9a56e 80%,#b88a52 100%)" role="img" aria-label="Woman on a beach holding a scarf in the wind at sunset"></div>
  <div class="abs hero-caption">Lorem <em>Ipsum</em> Dolor <em>Sit</em> <em>Amet</em></div>
  <div class="abs arrows"><svg width="6" height="10"><path d="M5 1 1 5l4 4" fill="none" stroke="#fff" stroke-width="1.5"/></svg><svg width="6" height="10"><path d="M1 1l4 4-4 4" fill="none" stroke="#fff" stroke-width="1.5"/></svg></div>
  <div class="abs meta" style="left:69px;top:290px"><svg width="9" height="9"><use href="#clock"/></svg>JULY 02, 2016 &nbsp;|&nbsp; BY &nbsp;<strong>Lorem Ipsum</strong></div>
  <h1 class="abs title" style="left:70px;top:310px">Lorem Ipsum Dolor Sit Amet</h1>
  <p class="abs excerpt" style="left:70px;top:330px;width:360px">Lorem ipsum dolor sit amet, consectetuer adipiscing elit, sed diam nonummy nibh euismod tincidunt ut laoreet dolore magna aliquam erat volutpat.</p>
  <div class="abs btn" style="left:69px;top:362px">READ MORE</div>
  <div class="abs rule" style="left:69px;top:401px;width:357px"></div>

  <div class="abs photo" style="left:69px;top:421px;width:167px;height:108px;background:linear-gradient(135deg,#f3e7a0,#a9d8b6 60%,#5fb9a3)" role="img" aria-label="Woman with arms open in soft sunlight"></div>
  <div class="abs photo" style="left:259px;top:421px;width:167px;height:108px;background:linear-gradient(180deg,#6f9ac4,#f4c36a 55%,#3a3a3a)" role="img" aria-label="Man raising arms against a sunset sky"></div>
  <div class="abs meta" style="left:69px;top:540px"><svg width="9" height="9"><use href="#clock"/></svg>JULY 02, 2016 &nbsp;|&nbsp; BY &nbsp;<strong>Lorem Ipsum</strong></div>
  <div class="abs meta" style="left:259px;top:540px"><svg width="9" height="9"><use href="#clock"/></svg>JULY 02, 2016 &nbsp;|&nbsp; BY &nbsp;<strong>Lorem Ipsum</strong></div>
  <h2 class="abs title" style="left:70px;top:560px;font-size:14px">Lorem Ipsum Dolor Sit.</h2>
  <h2 class="abs title" style="left:259px;top:560px;font-size:14px">Lorem Ipsum Dolor Sit.</h2>
  <p class="abs excerpt" style="left:70px;top:580px;width:170px">Lorem ipsum dolor sit amet, cetuer adipiscing elit.</p>
  <p class="abs excerpt" style="left:259px;top:580px;width:170px">Lorem ipsum dolor sit amet, cetuer adipiscing elit.</p>
  <div class="abs btn" style="left:69px;top:612px">READ MORE</div>
  <div class="abs btn" style="left:259px;top:612px">READ MORE</div>
  <div class="abs rule" style="left:69px;top:651px;width:357px"></div>

  <div class="abs meta" style="left:69px;top:670px"><svg width="9" height="9"><use href="#clock"/></svg>JULY 02, 2016 &nbsp;|&nbsp; BY &nbsp;<strong>Lorem Ipsum</strong></div>
  <div class="abs photo" style="left:69px;top:687px;width:162px;height:91px;background:linear-gradient(180deg,#7e9fc0,#d9c79a 55%,#a0902d 75%,#4f5a1e)" role="img" aria-label="Girl with outstretched arms in a yellow field"></div>
  <h2 class="abs title" style="left:242px;top:686px;width:190px;font-size:13px;line-height:16px">Lorem ipsum dolor sit amet, consectetuer adipiscing elit</h2>
  <p class="abs excerpt" style="left:242px;top:724px;width:190px">Lorem ipsum dolor sit amet, consectetue adipiscing elit, sed diam nonummy nibh.</p>
  <div class="abs btn" style="left:242px;top:757px">READ MORE</div>
  <div class="abs rule" style="left:69px;top:798px;width:357px"></div>

  <div class="abs meta" style="left:69px;top:814px"><svg width="9" height="9"><use href="#clock"/></svg>JULY 02, 2016 &nbsp;|&nbsp; BY &nbsp;<strong>Lorem Ipsum</strong></div>
  <div class="abs photo" style="left:69px;top:830px;width:162px;height:92px;background:linear-gradient(180deg,#c6d4dc,#f3e3b0 50%,#8a8f3e 72%,#3f4a20)" role="img" aria-label="Two people jumping in a sunny meadow"></div>
  <h2 class="abs title" style="left:242px;top:829px;width:190px;font-size:13px;line-height:16px">Lorem ipsum dolor sit amet, consectetuer adipiscing elit</h2>
  <p class="abs excerpt" style="left:242px;top:866px;width:190px">Lorem ipsum dolor sit amet, consectetue adipiscing elit, sed diam nonummy nibh.</p>
  <div class="abs btn" style="left:242px;top:899px">READ MORE</div>
  <div class="abs load"><svg width="10" height="10" viewBox="0 0 10 10"><g stroke="#f04924" stroke-width="1.3"><path d="M5 0v3M5 7v3M0 5h3M7 5h3M1.5 1.5l2 2M6.5 6.5l2 2M8.5 1.5l-2 2M3.5 6.5l-2 2"/></g></svg>Load More Blog</div>
</main>

<aside>
  <div class="abs widget-head" style="left:448px;top:80px"><svg width="155" height="19"><use href="#banner"/></svg><span>NEWSLETTER SIGNUP</span></div>
  <p class="abs" style="left:448px;top:107px;font-size:9.5px">Lorem Ipsum Dolor Sit Amet.</p>
  <div class="abs search" style="left:448px;top:128px;width:170px"><span style="color:#333">Search...</span><b style="width:25px"><svg width="9" height="9"><use href="#glass"/></svg></b></div>
  <div class="abs rule" style="left:448px;top:162px;width:170px"></div>
  <div class="abs photo" style="left:448px;top:182px;width:170px;height:136px;background:linear-gradient(180deg,#2c4b8c,#7d92c4 50%,#d8c2c8 80%,#5a6aa0)" role="img" aria-label="Advertisement with a climber on a rock face"></div>

  <div class="abs widget-head" style="left:448px;top:357px"><svg width="155" height="19"><use href="#banner"/></svg><span>MOST POPULAR</span></div>
  <div class="abs" style="left:594px;top:359px;display:flex;gap:2px"><svg width="11" height="11"><circle cx="5.5" cy="5.5" r="5" fill="none" stroke="#444"/><path d="M6.5 3 4 5.5 6.5 8" fill="none" stroke="#444"/></svg><svg width="11" height="11"><circle cx="5.5" cy="5.5" r="5" fill="none" stroke="#444"/><path d="M4.5 3 7 5.5 4.5 8" fill="none" stroke="#444"/></svg></div>

  <div class="abs avatar" style="left:448px;top:390px;background:linear-gradient(180deg,#5f93cf,#b8c9a4 60%,#6a8a2c)" role="img" aria-label="Person celebrating in a field"></div>
  <div class="abs" style="left:513px;top:401px;width:110px"><div class="pop-title">LOREM IPSUM DOLOR</div><p class="pop-text">Phasellus eget luctus metus. Vestibulum bibendum...</p></div>
  <div class="abs rule" style="left:448px;top:458px;width:170px"></div>
  <div class="abs" style="left:449px;top:484px;width:110px"><div class="pop-title">LOREM IPSUM DOLOR</div><p class="pop-text">Phasellus eget luctus metus. Vestibulum bibendum...</p></div>
  <div class="abs avatar" style="left:565px;top:474px;background:linear-gradient(180deg,#9fc1e0,#e0e3d0 55%,#5e8c34)" role="img" aria-label="Man with raised arms on a green hill"></div>
  <div class="abs rule" style="left:448px;top:542px;width:170px"></div>
  <div class="abs avatar" style="left:448px;top:554px;background:linear-gradient(180deg,#e8d3b0,#f4ece0 60%,#b9a27a)" role="img" aria-label="Smiling woman outdoors"></div>
  <div class="abs" style="left:513px;top:564px;width:110px"><div class="pop-title">LOREM IPSUM DOLOR</div><p class="pop-text">Phasellus eget luctus metus. Vestibulum bibendum...</p></div>
  <div class="abs rule" style="left:448px;top:628px;width:170px"></div>

  <div class="abs widget-head" style="left:448px;top:646px"><svg width="155" height="19"><use href="#banner"/></svg><span>TAGS</span></div>
  <div class="abs tags"><span>LOREM</span><span>LOREM IPSU</span><span>REM IPSU DOLOR</span><span>LOREM IPSU</span><span>REM IPSU</span><span>LOREM DOL</span><span>LOREM IPSUM DO</span><span>REM IPSU</span></div>
  <div class="abs" style="left:448px;top:756px;width:170px;height:1px;background:var(--navy)"></div>

  <div class="abs widget-head" style="left:448px;top:775px"><svg width="155" height="19"><use href="#banner"/></svg><span>ARCHIVE</span></div>
  <ul class="abs archive">
    <li><svg width="5" height="8"><path d="M1 1l3 3-3 3" fill="none" stroke="#24395f" stroke-width="1.2"/></svg>JULY 2016</li>
    <li><svg width="5" height="8"><path d="M1 1l3 3-3 3" fill="none" stroke="#24395f" stroke-width="1.2"/></svg>JUNE 2016</li>
    <li><svg width="5" height="8"><path d="M1 1l3 3-3 3" fill="none" stroke="#24395f" stroke-width="1.2"/></svg>MAY 2016</li>
    <li><svg width="5" height="8"><path d="M1 1l3 3-3 3" fill="none" stroke="#24395f" stroke-width="1.2"/></svg>APR 2016</li>
    <li><svg width="5" height="8"><path d="M1 1l3 3-3 3" fill="none" stroke="#24395f" stroke-width="1.2"/></svg>MARCH 2016</li>
    <li><svg width="5" height="8"><path d="M1 1l3 3-3 3" fill="none" stroke="#24395f" stroke-width="1.2"/></svg>FEB 2016</li>
    <li><svg width="5" height="8"><path d="M1 1l3 3-3 3" fill="none" stroke="#24395f" stroke-width="1.2"/></svg>JAN 2016</li>
  </ul>
</aside>

<section class="abs about">
  <div class="abs photo" style="left:69px;top:12px;width:157px;height:158px;border:2px solid #c9c9c9;background:linear-gradient(180deg,#4a5872,#8a93a6 50%,#24395f)" role="img" aria-label="Portrait of the author"></div>
  <h2 class="abs">About Me</h2>
  <p class="abs">Lorem ipsum dolor sit amet, consectetuer adipiscing elit, sed diam nonummy nibh euismod alme tincidunt ut laoreet dolore magna aliquam erat volutpat. Ut wisi enim ad minim veniam, quis dol nostrud exerci tation ullamcorper suscipit lobortis nisl ut aliquip ex ea commodo consequat list Duis autem vel eum iriure dolor in hendrerit in vulputate velit esse molestie consequat, vel alm illum dolore eu feugiat nulla facilisis at vero eros et accumsan et iusto odio dignissim qui blandit illum dolore eu feugiat nulla facilisis at vero eros et accumsan et vel eum iriure dolor in hendrerit in</p>
  <div class="abs btn" style="left:248px;top:145px">READ MORE</div>
</section>

<footer class="abs footer">Copyright © 2016 Tandem K. All Rights Reserved.</footer>
</body>
</html>
```